Marcus Delbridge Finance

Need a personal website advertising Equipment Finance,Business Finance,Commercial Finance, Construction Finance, Bridging Finance. Similar websites are www.corvalend.com.au / www.tarmivest.com.au / www.qbr7.com.au /wwwhalvecredit.com.au

Target Market(s)

Business People

Industry/Entity Type

Business

Number of Pages Required

3 page

Font styles to use
Serif
Sans Serif

Requirements
Must have
• All i want is a simple corporate looking website advertising Equipment Finance, Commercial Finance, Construction Finance, Business Finance, Bridging Finance,

```html
<!DOCTYPE html>
<html lang="en">
<head>
<meta charset="utf-8">
<title>Marcus Delbridge Finance</title>
<link href="https://fonts.googleapis.com/css2?family=Tinos:ital,wght@0,400;0,700;1,400&family=Raleway:wght@400;500&family=Arimo:ital,wght@0,400;0,700;1,400&family=Open+Sans:wght@400;600&display=swap" rel="stylesheet">
<style>
:root{
  --navy:#1c4f8a;
  --navy-dark:#123b6b;
  --blue:#1d6fb8;
  --footer:#0f5296;
  --ink:#222;
  --grey:#555;
  --light:#e9e9e9;
  --charcoal:#2b2b2b;
  --white:#fff;
  --serif:"Tinos", "Times New Roman", serif;
  --sans:"Arimo", Arial, sans-serif;
  --open:"Open Sans", Arial, sans-serif;
  --display:"Raleway", Arial, sans-serif;
}
*{box-sizing:border-box;margin:0;padding:0}
html,body{width:1200px;height:2594px;overflow:hidden;background:var(--white)}
body{position:relative;font-family:var(--sans);color:var(--ink)}
.abs{position:absolute}

/* header */
.topstrip{left:743px;top:0;width:457px;height:35px;background:var(--light);border-bottom-left-radius:30px}
.topstrip .call{position:absolute;left:12px;top:6px;display:flex;align-items:center;gap:10px;font:13px var(--sans);color:#333}
.dot-icon{width:24px;height:24px;border-radius:50%;background:var(--navy-dark);display:inline-block}
.social-top{position:absolute;left:172px;top:5px;display:flex;gap:5px}
.brand{left:170px;top:44px;display:flex;align-items:center;gap:12px}
.brand .mark{width:34px;height:34px;background:var(--navy)}
.brand .name{font:700 21px var(--serif);color:var(--navy);letter-spacing:.5px}
.search{left:788px;top:59px;width:249px;height:36px;border:1px solid #ccc;display:flex}
.search span{flex:1;font:12px var(--serif);color:#999;padding:10px 8px}
.search b{width:38px;background:var(--navy-dark);display:flex;align-items:center;justify-content:center}
.nav{left:0;top:116px;width:1200px;height:43px;background:linear-gradient(#2a5f9c,#123f73)}
.nav ul{list-style:none;display:flex;justify-content:center;gap:30px;padding-top:11px;padding-left:0}
.nav li{font:14px var(--serif);color:var(--white)}

/* hero */
.hero{left:0;top:159px;width:1200px;height:501px;background:radial-gradient(ellipse at 70% 35%,#caa36b 0%,#7a6048 30%,#3d3530 60%,#1e1c1b 100%)}
.hero .caption{position:absolute;left:0;bottom:0;width:100%;height:58px;background:rgba(0,0,0,.45);font:400 27px var(--display);color:var(--white);text-align:center;line-height:58px}
.arrow{position:absolute;top:226px;width:30px;height:28px;background:#3a3a3a;border:1px solid #888;display:flex;align-items:center;justify-content:center}

/* about */
.about-title{left:0;top:690px;width:1200px;text-align:center;font:32px var(--serif);color:#111}
.about-title em{font-style:normal;color:var(--blue)}
.rule{height:1px;background:#bbb}
.rule i{display:block;margin:-1px auto 0;width:34px;height:3px;background:var(--navy)}
.about-text{left:173px;top:778px;width:854px;text-align:center;font:11px/18px var(--sans);color:#333}

/* services */
.services{left:0;top:900px}
.hex-label{font-family:var(--serif);font-size:17px;fill:var(--white)}

/* why */
.why{left:0;top:1409px;width:1200px;height:432px;background:var(--navy);overflow:hidden}
.why h2{position:absolute;left:0;top:40px;width:100%;text-align:center;font:400 29px var(--serif);color:var(--white)}
.why .rule{position:absolute;left:540px;top:85px;width:124px;background:#6a8fbd}
.reason{position:absolute;color:var(--white)}
.reason h3{font:700 16px/19px var(--serif)}
.reason p{font:11px/16px var(--open);margin-top:3px}
.reason.l{text-align:right}
.why-name{position:absolute;left:452px;top:330px;width:300px;text-align:center;font:700 22px var(--serif);color:var(--navy)}

/* testimonials */
.test-title{left:0;top:1906px;width:1200px;text-align:center;font:29px var(--serif);color:#111}
.test-title em{font-style:normal;color:var(--blue)}
.quote{left:225px;top:1988px;width:778px;text-align:center;font:italic 14px/26px var(--sans);color:#333}
.qmark{font:60px var(--serif);color:#bbb;position:absolute}
.person{left:0;top:2079px;width:1200px;text-align:center}
.person b{display:block;font:600 14px var(--open);color:var(--blue)}
.person span{font:13px var(--open);color:#333}
.dots{left:572px;top:2143px;display:flex;gap:7px}
.dots i{width:7px;height:7px;border-radius:50%;background:#999}
.dots i:first-child{background:var(--navy)}

/* newsletter */
.news{left:0;top:2199px;width:1200px;height:66px;background:linear-gradient(#4a4a4a,#1c1c1c 60%,#2a2a2a)}
.news .label{position:absolute;left:256px;top:17px;font:25px var(--serif);color:var(--white)}
.news .field{position:absolute;left:660px;top:16px;width:260px;height:31px;background:var(--white);font:11px var(--open);color:#444;padding:8px 9px}
.news .btn{position:absolute;left:920px;top:16px;width:121px;height:31px;background:var(--footer);font:13px var(--open);color:var(--white);text-align:center;line-height:31px}

/* footer */
.footer{left:0;top:2265px;width:1200px;height:282px;background:var(--footer);color:var(--white)}
.fcol{position:absolute;top:44px}
.fcol h4{font:400 17px var(--serif);margin-bottom:16px}
.fcol ul{list-style:none}
.fcol li{font:12px/22px var(--serif)}
.fcol li::before{content:"› ";}
.divider{position:absolute;top:50px;width:1px;height:200px;background:rgba(255,255,255,.2)}
.contact-row{display:flex;align-items:flex-start;gap:10px;font:12px/17px var(--serif);margin-bottom:19px}
.cicon{width:16px;height:16px;border-radius:50%;background:var(--white);flex:none}
.inq-field{width:210px;height:32px;background:var(--white);margin-bottom:6px;font:10px var(--open);color:#444;padding:9px 8px}
.inq-field.msg{height:62px}
.submit{width:104px;height:32px;background:#111;font:14px var(--serif);color:var(--white);line-height:32px;padding-left:14px}
.social-foot{display:flex;gap:6px}
.social-foot i{width:32px;height:32px;border-radius:50%;background:var(--white);border:2px solid #8fb3dc}
.faint-name{margin-top:24px;font:700 20px/24px var(--serif);color:rgba(255,255,255,.25);width:150px}
.copy{left:0;top:2547px;width:1200px;height:47px;background:#3a3a3a;text-align:center;font:12px/47px var(--serif);color:#ddd}
</style>
</head>
<body>

<header>
  <div class="abs topstrip">
    <div class="call"><span class="dot-icon"></span>Call : 123-456-7890</div>
    <div class="social-top"><span class="dot-icon"></span><span class="dot-icon"></span><span class="dot-icon"></span><span class="dot-icon"></span></div>
  </div>
  <div class="abs brand"><span class="mark"></span><span class="name">MARCUS DELBRIDGE FINANCE</span></div>
  <div class="abs search"><span>Search here...</span><b><svg width="16" height="16" viewBox="0 0 16 16"><circle cx="6.5" cy="6.5" r="5" fill="none" stroke="#fff" stroke-width="2"/><line x1="10" y1="10" x2="15" y2="15" stroke="#fff" stroke-width="2"/></svg></b></div>
  <nav class="abs nav"><ul><li>Home</li><li>Equipment Finance</li><li>Business Finance</li><li>Commercial Finance</li><li>Construction Finance</li><li>Bridging Finance</li><li>Contact Us</li></ul></nav>
</header>

<section class="abs hero" role="img" aria-label="Excavator working on a site at sunset">
  <div class="arrow" style="left:4px"><svg width="10" height="12"><path d="M8 1 3 6l5 5" stroke="#fff" stroke-width="2" fill="none"/></svg></div>
  <div class="arrow" style="right:4px"><svg width="10" height="12"><path d="M2 1l5 5-5 5" stroke="#fff" stroke-width="2" fill="none"/></svg></div>
  <div class="caption">Focus on What you do Best, While We take care of your finances</div>
</section>

<section>
  <h1 class="abs about-title">About Marcus Delbridge <em>- Finance</em></h1>
  <div class="abs rule" style="left:472px;top:744px;width:256px"><i></i></div>
  <p class="abs about-text">Lorem ipsum dolor sit amet, consectetuer adipiscing elit, sed diam nonummy nibh euismod tincidunt ut laoreet dolore magna aliquam erat volutpat. Ut wisi enim ad minim veniam, quis nostrud exerci tation ullamcorper suscipit lobortis nisl ut aliquip ex ea commodo consequat. Duis autem vel eum iriure dolor in hendrerit in vulputate velit esse molestie consequat, vel illum dolore eu feugiat nulla facilisis at vero eros et accumsan et iusto odio dignissim qui blandit praesent luptatum zzril delenit augue duis dolore te feugait nulla facilisi.</p>
</section>

<section class="abs services">
  <svg width="1200" height="480" viewBox="0 900 1200 480">
    <defs>
      <linearGradient id="gEquip" x1="0" y1="0" x2="0" y2="1"><stop offset="0" stop-color="#5f7ea6"/><stop offset="1" stop-color="#3a3a36"/></linearGradient>
      <linearGradient id="gBiz" x1="0" y1="0" x2="1" y2="1"><stop offset="0" stop-color="#c9d6e6"/><stop offset="1" stop-color="#5b7fae"/></linearGradient>
      <linearGradient id="gComm" x1="0" y1="0" x2="0" y2="1"><stop offset="0" stop-color="#3b5a82"/><stop offset="1" stop-color="#1c2b40"/></linearGradient>
      <linearGradient id="gCons" x1="0" y1="0" x2="0" y2="1"><stop offset="0" stop-color="#8fb2d8"/><stop offset="1" stop-color="#4c4a4c"/></linearGradient>
      <linearGradient id="gBridge" x1="0" y1="0" x2="0" y2="1"><stop offset="0" stop-color="#9fb4c8"/><stop offset="1" stop-color="#7d7468"/></linearGradient>
      <linearGradient id="gOther" x1="0" y1="0" x2="1" y2="1"><stop offset="0" stop-color="#e4e4e4"/><stop offset="1" stop-color="#a9b1bd"/></linearGradient>
    </defs>
    <g stroke="#dedede" stroke-width="8" stroke-linejoin="round">
      <polygon role="img" aria-label="Excavator on a construction site" fill="url(#gEquip)" points="380,922 480,980 480,1094 380,1152 280,1094 280,980"/>
      <polygon fill="var(--navy)" points="602,922 702,980 702,1094 602,1152 502,1094 502,980"/>
      <polygon role="img" aria-label="Hands reviewing business charts" fill="url(#gBiz)" points="825,922 925,980 925,1094 825,1152 725,1094 725,980"/>
      <polygon role="img" aria-label="Business handshake" fill="url(#gComm)" points="263,1121 363,1179 363,1293 263,1351 163,1293 163,1179"/>
      <polygon role="img" aria-label="Building under construction with crane" fill="url(#gCons)" points="491,1121 591,1179 591,1293 491,1351 391,1293 391,1179"/>
      <polygon role="img" aria-label="Stacked stones forming an arch" fill="url(#gBridge)" points="718,1121 818,1179 818,1293 718,1351 618,1293 618,1179"/>
      <polygon role="img" aria-label="People signing documents" fill="url(#gOther)" points="935,1121 1035,1179 1035,1293 935,1351 835,1293 835,1179"/>
    </g>
    <text x="602" y="1037" text-anchor="middle" font-family="Tinos, serif" font-size="38" fill="#fff">Our</text>
    <text x="602" y="1080" text-anchor="middle" font-family="Tinos, serif" font-size="38" fill="#fff">Services</text>
    <text class="hex-label" x="380" y="1107" text-anchor="middle">Equipment Finance</text>
    <text class="hex-label" x="835" y="1112" text-anchor="middle">Business Finance</text>
    <text class="hex-label" x="260" y="1306" text-anchor="middle">Commercial Finance</text>
    <text class="hex-label" x="493" y="1306" text-anchor="middle">Construction Finance</text>
    <text class="hex-label" x="718" y="1303" text-anchor="middle">Bridging Finance</text>
    <text class="hex-label" x="935" y="1306" text-anchor="middle">Others</text>
  </svg>
</section>

<section class="abs why">
  <h2>Why Choose Us</h2>
  <div class="rule"><i style="background:#fff"></i></div>
  <svg class="abs" style="left:0;top:0" width="1200" height="432" viewBox="0 1409 1200 432">
    <g stroke="#fff" stroke-width="2" stroke-dasharray="2 4" fill="none">
      <line x1="533" y1="1613" x2="558" y2="1672"/>
      <line x1="429" y1="1665" x2="488" y2="1722"/>
      <line x1="380" y1="1767" x2="446" y2="1795"/>
      <line x1="662" y1="1613" x2="644" y2="1672"/>
      <line x1="762" y1="1665" x2="716" y2="1722"/>
      <line x1="821" y1="1764" x2="758" y2="1795"/>
    </g>
    <circle cx="602" cy="1867" r="168" fill="#fff" stroke="#3e7cc4" stroke-width="6"/>
    <g fill="#fff" stroke="var(--navy)" stroke-width="2">
      <circle cx="558" cy="1683" r="6"/><circle cx="644" cy="1683" r="6"/>
      <circle cx="492" cy="1726" r="6"/><circle cx="712" cy="1726" r="6"/>
      <circle cx="446" cy="1795" r="6"/><circle cx="758" cy="1795" r="6"/>
    </g>
    <g fill="#fff">
      <circle cx="533" cy="1613" r="34"/><circle cx="429" cy="1665" r="34"/><circle cx="380" cy="1767" r="34"/>
      <circle cx="662" cy="1613" r="34"/><circle cx="762" cy="1665" r="34"/><circle cx="821" cy="1764" r="34"/>
    </g>
    <g fill="var(--navy)">
      <path d="M519 1600c3-3 6-3 8 0l4 5c1 2 0 4-2 5l-2 2c2 5 6 9 11 11l2-2c1-2 3-3 5-2l5 4c3 2 3 5 0 8-7 7-16 3-24-5s-12-19-7-26z"/>
      <circle cx="429" cy="1665" r="10" fill="none" stroke="var(--navy)" stroke-width="6" stroke-dasharray="4 3"/>
      <circle cx="429" cy="1665" r="4"/>
      <circle cx="380" cy="1762" r="11"/><rect x="374" y="1774" width="12" height="8"/>
      <circle cx="660" cy="1602" r="9"/><path d="M644 1632c0-12 8-18 18-18s18 6 18 18z"/>
      <rect x="748" y="1651" width="26" height="24" rx="2"/><rect x="752" y="1660" width="18" height="11" fill="#fff"/>
      <circle cx="813" cy="1756" r="6"/><circle cx="829" cy="1756" r="6"/><path d="M803 1778c0-9 5-14 10-14s10 5 10 14zM819 1778c0-9 5-14 10-14s10 5 10 14z"/>
    </g>
  </svg>
  <div class="reason l" style="left:180px;top:121px;width:300px"><h3>Unbiased Recommendations</h3><p>Lorem ipsum dolor sit amet<br>adipiscing sed diam [+]</p></div>
  <div class="reason l" style="left:175px;top:206px;width:200px"><h3>Unparalleled<br>Service</h3><p>Lorem ipsum dolor sit amet<br>adipiscing sed diam [+]</p></div>
  <div class="reason l" style="left:120px;top:331px;width:202px"><h3>Superior Advice</h3><p>Lorem ipsum dolor sit amet<br>adipiscing sed diam [+]</p></div>
  <div class="reason" style="left:720px;top:121px;width:250px"><h3>Expert Guidance</h3><p>Lorem ipsum dolor sit amet<br>adipiscing sed diam [+]</p></div>
  <div class="reason" style="left:825px;top:206px;width:250px"><h3>Considerable Time<br>For You</h3><p>Lorem ipsum dolor sit amet<br>adipiscing sed diam [+]</p></div>
  <div class="reason" style="left:877px;top:315px;width:250px"><h3>Deep Legal Industry<br>Relationships</h3><p>Lorem ipsum dolor sit amet<br>adipiscing sed diam [+]</p></div>
  <div class="why-name">Marcus Delbridge Finance</div>
</section>

<section>
  <h2 class="abs test-title">Clients <em>Testimonials</em></h2>
  <div class="abs rule" style="left:480px;top:1960px;width:240px"><i></i></div>
  <svg class="abs" style="left:132px;top:2007px" width="30" height="50"><path d="M26 2 4 25l22 23" stroke="#9aa4b3" stroke-width="1.5" fill="none"/></svg>
  <svg class="abs" style="left:1038px;top:2007px" width="30" height="50"><path d="M4 2l22 23L4 48" stroke="#9aa4b3" stroke-width="1.5" fill="none"/></svg>
  <span class="qmark" style="left:193px;top:1962px">“</span>
  <span class="qmark" style="left:768px;top:2024px">”</span>
  <p class="abs quote">Lorem ipsum dolor sit amet, consectetuer adipiscing elit, sed diam nonummy nibh euismod tinciduntol ut laoreet dolore magna aliquam erat volutpat. Ut wisi enim ad minim veniam, quis nostrud exercimori mornkle tation ullamcorper suscipit lobortis nisl ut aliquip ex ea commodo consequat.</p>
  <div class="abs person"><b>Rowan T.</b><span>Harbor Point, CA</span></div>
  <div class="abs dots"><i></i><i></i><i></i><i></i></div>
</section>

<section class="abs news">
  <svg class="abs" style="left:162px;top:14px" width="80" height="40" viewBox="0 0 80 40"><rect x="18" y="4" width="50" height="30" fill="none" stroke="#fff" stroke-width="3" transform="rotate(-12 43 19)"/><path d="M20 10l24 14 22-18" fill="none" stroke="#fff" stroke-width="2" transform="rotate(-12 43 19)"/><g stroke="#fff" stroke-width="2"><line x1="2" y1="18" x2="14" y2="18"/><line x1="6" y1="24" x2="16" y2="24"/><line x1="4" y1="30" x2="18" y2="30"/></g></svg>
  <div class="label">Subscribe Our Newsletter</div>
  <svg class="abs" style="left:570px;top:22px" width="72" height="24"><path d="M2 18c22 4 44 2 64-12" stroke="#fff" stroke-width="1.5" fill="none"/><path d="M58 4l9 2-4 8" stroke="#fff" stroke-width="1.5" fill="none"/></svg>
  <div class="field">Enter Your Email Address</div>
  <div class="btn">SUBSCRIBE</div>
</section>

<footer class="abs footer">
  <div class="fcol" style="left:164px"><h4>Quick Links</h4><ul><li>Home</li><li>Equipment Finance</li><li>Business Finance</li><li>Commercial Finance</li><li>Construction Finance</li><li>Bridging Finance</li><li>Contact Us</li></ul></div>
  <div class="divider" style="left:340px"></div>
  <div class="fcol" style="left:360px">
    <h4>Contact Details</h4>
    <div class="abs" role="img" aria-label="Faint world map" style="left:60px;top:60px;width:170px;height:100px;background:radial-gradient(ellipse,rgba(255,255,255,.12),rgba(255,255,255,0) 70%)"></div>
    <div class="contact-row"><span class="cicon"></span><span>Marcus Delbridge Finance<br>Street Name City Name<br>State Zipcode</span></div>
    <div class="contact-row"><span class="cicon"></span><span>123-456-7890</span></div>
    <div class="contact-row"><span class="cicon"></span><span>123-456-7890</span></div>
    <div class="contact-row"><span class="cicon"></span><span>inquiry@delbridgefinance.com</span></div>
  </div>
  <div class="divider" style="left:585px"></div>
  <div class="fcol" style="left:609px"><h4>Quick Inquiry</h4><div class="inq-field">Name</div><div class="inq-field">Email</div><div class="inq-field msg">Message</div><div class="submit">Submit &nbsp;→</div></div>
  <div class="divider" style="left:830px"></div>
  <div class="fcol" style="left:851px"><h4>Follow Us</h4><div class="social-foot"><i></i><i></i><i></i><i></i></div><div class="faint-name">Marcus Delbridge Finance</div></div>
</footer>
<div class="abs copy">Copyright © 2017 Marcus Delbridge Finance. All Rights Reserved.</div>

</body>
</html>
```